CBD/HEMP website for e-commerce store

I need a CBD website for my shopify store. I am looking for a layout similar to these site ( https://quietmeadowcbd.com/ ) (https://elmridgecbd.com/) but with my logo and products. I am attaching what my logo looks like so that it helps with the design.

Target Market(s)

CBD HEMP CANNABIS

Industry/Entity Type

Cannabis

Coding

Coded - Design and coding required

Number of Pages Required

5+ page

Requirements
Nice to have
• I would like for it to have a trendy/galaxy feel

```html
<!DOCTYPE html>
<html lang="en">
<head>
<meta charset="utf-8">
<title>Velvet Orbit – The Ultimate Cannabis Experience</title>
<link href="https://fonts.googleapis.com/css2?family=Playfair+Display:wght@400;700&family=Open+Sans:wght@400;600;700&display=swap" rel="stylesheet">
<style>
:root{
  --pink:#d4317c;
  --pink-dark:#b0215f;
  --blush:#fbeef4;
  --night:#171321;
  --night-2:#241a3a;
  --ink:#222;
  --muted:#666;
  --star:#f2b01e;
  --white:#fff;
  --serif:"Playfair Display",Georgia,serif;
  --sans:"Open Sans",Arial,sans-serif;
}
*{box-sizing:border-box;margin:0;padding:0}
html,body{width:1200px;height:3700px;overflow:hidden}
body{font-family:var(--sans);color:var(--ink);background:var(--white)}
.btn{display:inline-block;background:var(--pink);color:var(--white);font-size:13px;font-weight:700;letter-spacing:1px;text-transform:uppercase;padding:11px 30px;border-radius:3px}
.btn.small{font-size:11px;padding:8px 22px}

/* top bar */
.topbar{height:32px;background:#0d0a14;color:var(--white);font-size:11px;letter-spacing:1.5px;text-align:center;line-height:32px;text-transform:uppercase}

/* hero */
.hero{position:relative;height:488px;background:radial-gradient(ellipse at 55% 30%,#7a2e8f 0%,#3a1659 35%,#150b26 75%);color:var(--white);overflow:hidden}
.nav{display:flex;align-items:center;justify-content:space-between;padding:0 40px;height:70px;font-size:11px;font-weight:600;letter-spacing:1.5px;text-transform:uppercase}
.nav ul{display:flex;gap:34px;list-style:none}
.brand{display:flex;align-items:center;gap:10px;font-size:20px;font-weight:700;letter-spacing:2px}
.brand .dot{width:14px;height:14px;border-radius:50%;background:var(--pink)}
.hero-copy{text-align:center;margin-top:70px}
.hero-copy h1{font-family:var(--serif);font-weight:400;font-size:50px;letter-spacing:4px;line-height:1.1}
.hero-copy h1 span{display:block;font-size:34px;letter-spacing:3px}
.hero-copy .btn{margin-top:24px}
.hero-buds{position:absolute;left:0;right:0;bottom:0;height:130px;background:linear-gradient(180deg,rgba(0,0,0,0),#4c6b2a 45%,#2f4519)}
.arrow{position:absolute;top:260px;font-size:28px;opacity:.7}
.arrow.l{left:24px}.arrow.r{right:24px}

/* reviews */
.reviews{height:240px;background:var(--blush);padding:36px 40px}
.reviews-head{display:flex;justify-content:space-between;align-items:center;border-bottom:1px solid #e3cfd9;padding-bottom:12px}
.reviews-head h2{font-size:15px;font-weight:700;letter-spacing:1px;text-transform:uppercase}
.reviews-head .pager{font-size:20px;color:var(--muted)}
.review-row{display:grid;grid-template-columns:repeat(4,1fr);gap:24px;margin-top:20px}
.review .meta{font-size:10px;color:var(--muted)}
.stars{color:var(--star);letter-spacing:1px;font-size:12px}
.review h3{font-size:13px;font-weight:700;margin:4px 0 8px}
.review .body{display:flex;gap:10px}
.review .thumb{flex:0 0 44px;height:44px;border-radius:4px;background:radial-gradient(circle,#8faa4e,#4c6a2a)}
.review p{font-size:10px;line-height:1.5;color:var(--muted)}
.review .more{font-size:10px;font-weight:700;margin-top:6px}

/* products */
.products{height:620px;padding-top:70px;text-align:center}
.eyebrow{font-size:12px;font-weight:700;letter-spacing:2px;text-transform:uppercase}
.section-title{font-family:var(--serif);font-weight:400;font-size:42px;letter-spacing:2px;margin-top:4px}
.product-row{display:grid;grid-template-columns:repeat(4,224px);gap:24px;justify-content:center;margin-top:38px;text-align:left}
.product .pic{height:250px;border-radius:2px}
.pic.bud{background:radial-gradient(circle at 50% 50%,#a4b873 0%,#6f8a3c 45%,#f3f3f3 72%)}
.pic.oil{background:radial-gradient(ellipse at 50% 55%,#c89a3a 0%,#5a6b2c 30%,#f3f3f3 60%)}
.product h3{font-size:14px;font-weight:700;margin-top:14px}
.product .price{font-size:11px;color:var(--muted);margin:3px 0}
.product .rating{font-size:10px;color:var(--muted)}
.products .btn{margin-top:34px}

/* categories */
.categories{height:520px;background:var(--blush);padding:60px 20px 0}
.cat-row{display:grid;grid-template-columns:repeat(3,1fr);gap:12px}
.cat{position:relative;height:400px;color:var(--white);overflow:hidden}
.cat.flowers{background:linear-gradient(160deg,#5e7b38,#2b3a1b)}
.cat.prerolls{background:linear-gradient(160deg,#c9c2c0,#6a4a50)}
.cat.vapes{background:linear-gradient(160deg,#9bb36f,#8a4a3a)}
.cat .label{position:absolute;left:30px;bottom:30px}
.cat small{font-size:10px;font-weight:700;letter-spacing:1.5px}
.cat h3{font-family:var(--serif);font-weight:400;font-size:40px;line-height:1;margin:2px 0 12px}

/* beyond */
.beyond{position:relative;height:550px;background:radial-gradient(ellipse at 50% 45%,#2d3b7a 0%,#1a1d47 40%,#0b0a1d 80%);color:var(--white);text-align:center;overflow:hidden}
.beyond .ring{position:absolute;left:50%;top:60px;width:400px;height:400px;margin-left:-200px;border-radius:50%;border:3px solid rgba(255,255,255,.85);box-shadow:0 0 40px rgba(180,200,255,.7),inset 0 0 40px rgba(180,200,255,.4)}
.beyond .leaf{width:110px;height:110px;margin:90px auto 0;border-radius:50%;background:radial-gradient(circle,#e6a3e0,#7a3a9c 60%,transparent 72%)}
.beyond h2{position:relative;font-family:var(--serif);font-weight:400;font-size:44px;margin-top:18px}
.beyond p{position:relative;width:560px;margin:14px auto 0;font-size:13px;line-height:1.6;color:#dfe2f5}
.beyond .btn{position:relative;margin-top:24px}

/* blog */
.blog{height:770px;background:var(--blush);padding-top:80px;text-align:center}
.blog-row{display:grid;grid-template-columns:repeat(3,330px);gap:40px;justify-content:center;margin-top:40px;text-align:left}
.post .pic{height:230px}
.pic.post1{background:linear-gradient(135deg,#d9cfc6,#5a6a3a)}
.pic.post2{background:linear-gradient(135deg,#8fa25a,#3c5a22)}
.pic.post3{background:linear-gradient(135deg,#b9a890,#6f8a4c)}
.post h3{font-family:var(--serif);font-weight:700;font-size:19px;line-height:1.35;margin-top:18px}
.post p{font-size:12px;line-height:1.6;color:var(--muted);margin-top:10px}
.post .read{font-size:11px;font-weight:700;letter-spacing:1px;margin-top:12px}
.blog .btn{margin-top:44px}

/* footer */
.footer{height:480px;background:var(--night);color:#cfcad8;padding:60px 60px 0;font-size:12px}
.footer-cols{display:grid;grid-template-columns:1.3fr 1fr 1.2fr;gap:60px}
.footer h4{color:var(--white);font-size:13px;font-weight:700;letter-spacing:1.5px;text-transform:uppercase;margin-bottom:16px}
.footer p{line-height:1.7;margin-bottom:12px}
.contact{display:flex;align-items:center;gap:10px;margin-bottom:10px}
.social{display:flex;gap:10px;margin-top:14px}
.social span{width:20px;height:20px;border-radius:50%;background:#4a4258}
.footer ul{list-style:none;line-height:2}
.field{border:1px solid #5a5268;color:#8f88a0;padding:12px 14px;margin:6px 0 14px}
.copy{text-align:center;border-top:1px solid #2e283c;margin-top:70px;padding-top:24px;color:#9a93aa}
</style>
</head>
<body>

<div class="topbar">Free shipping on all orders over $99</div>

<header class="hero">
  <nav class="nav">
    <ul><li>Shop</li><li>Reviews</li><li>Blog</li><li>Our Story</li><li>Wholesale</li></ul>
    <div class="brand"><span class="dot"></span>VELVET ORBIT</div>
    <ul><li>Account</li><li>Search</li><li>Cart (0)</li></ul>
  </nav>
  <div class="hero-copy">
    <h1>THE ULTIMATE<span>CANNABIS EXPERIENCE</span></h1>
    <a class="btn">Shop now</a>
  </div>
  <span class="arrow l">‹</span><span class="arrow r">›</span>
  <div class="hero-buds" role="img" aria-label="Row of cannabis flower buds along the bottom of a starry galaxy sky"></div>
</header>

<section class="reviews">
  <div class="reviews-head"><h2>Real reviews from real customers</h2><span class="pager">‹ ›</span></div>
  <div class="review-row">
    <article class="review"><div class="meta"><span class="stars">★★★★★</span> 03/12/2020</div><h3>I would definitely recommend this</h3><div class="body"><div class="thumb" role="img" aria-label="Cannabis bud"></div><div><p>Smooth taste and calm effect. Shipping was fast and the packaging felt premium.</p><div class="more">Learn more</div></div></div></article>
    <article class="review"><div class="meta"><span class="stars">★★★★★</span> 03/10/2020</div><h3>I would definitely recommend this</h3><div class="body"><div class="thumb" role="img" aria-label="CBD oil bottle"></div><div><p>Great quality oil that helps me relax after work. I will be ordering again soon.</p><div class="more">Learn more</div></div></div></article>
    <article class="review"><div class="meta"><span class="stars">★★★★★</span> 03/08/2020</div><h3>I would definitely recommend this</h3><div class="body"><div class="thumb" role="img" aria-label="Cannabis bud"></div><div><p>Fresh flower with a lovely aroma. Friendly support answered all my questions quickly.</p><div class="more">Learn more</div></div></div></article>
    <article class="review"><div class="meta"><span class="stars">★★★★★</span> 03/05/2020</div><h3>I would definitely recommend this</h3><div class="body"><div class="thumb" role="img" aria-label="Cannabis bud"></div><div><p>Consistent strength every time. This has become my favourite shop for hemp products.</p><div class="more">Learn more</div></div></div></article>
  </div>
</section>

<section class="products">
  <div class="eyebrow">Popular today</div>
  <h2 class="section-title">CBD PRODUCTS</h2>
  <div class="product-row">
    <div class="product"><div class="pic bud" role="img" aria-label="Light green cannabis bud"></div><h3>Product Name</h3><div class="price">Starting at $00</div><div class="rating"><span class="stars">★★★★★</span> 120 reviews</div></div>
    <div class="product"><div class="pic bud" role="img" aria-label="Cannabis bud close-up"></div><h3>Product Name</h3><div class="price">Starting at $00</div><div class="rating"><span class="stars">★★★★★</span> 98 reviews</div></div>
    <div class="product"><div class="pic oil" role="img" aria-label="CBD oil dropper bottle beside hemp leaf"></div><h3>Product Name</h3><div class="price">Starting at $00</div><div class="rating"><span class="stars">★★★★★</span> 76 reviews</div></div>
    <div class="product"><div class="pic bud" role="img" aria-label="Dense green cannabis bud"></div><h3>Product Name</h3><div class="price">Starting at $00</div><div class="rating"><span class="stars">★★★★★</span> 54 reviews</div></div>
  </div>
  <a class="btn">Shop now</a>
</section>

<section class="categories">
  <div class="cat-row">
    <div class="cat flowers" role="img" aria-label="Cannabis plant with frosty flowers"><div class="label"><small>CBD</small><h3>Flowers</h3><a class="btn small">Shop now</a></div></div>
    <div class="cat prerolls" role="img" aria-label="Person enjoying a pre-roll"><div class="label"><small>CBD</small><h3>Pre-Rolls</h3><a class="btn small">Shop now</a></div></div>
    <div class="cat vapes" role="img" aria-label="Person using a vape pen outdoors"><div class="label"><small>CBD</small><h3>Vapes</h3><a class="btn small">Shop now</a></div></div>
  </div>
</section>

<section class="beyond">
  <div class="ring"></div>
  <div class="leaf" role="img" aria-label="Glowing purple cannabis leaf"></div>
  <h2>Beyond the High</h2>
  <p>Lorem ipsum dolor sit amet, consectetur adipiscing elit, sed do eiusmod tempor incididunt ut labore et dolore magna aliqua. Quis ipsum suspendisse ultrices gravida. Risus commodo viverra maecenas accumsan lacus vel facilisis.</p>
  <a class="btn">Shop now</a>
</section>

<section class="blog">
  <div class="eyebrow">Blog</div>
  <h2 class="section-title">Shared Secrets</h2>
  <div class="blog-row">
    <article class="post"><div class="pic post1" role="img" aria-label="Hands preparing cannabis on a table"></div><h3>Lorem ipsum dolor sit amet or sit amet adipiscing elit, sed do eiusmod tempor</h3><p>Lorem ipsum dolor sit amet, consectetur adipiscing elit, sed do eiusmod tempor incididunt ut labore et dolore magna aliqua.</p><div class="read">READ MORE →</div></article>
    <article class="post"><div class="pic post2" role="img" aria-label="Cannabis buds with hemp leaves"></div><h3>Lorem ipsum dolor sit amet or sit amet adipiscing elit, sed do eiusmod tempor</h3><p>Lorem ipsum dolor sit amet, consectetur adipiscing elit, sed do eiusmod tempor incididunt ut labore et dolore magna aliqua.</p><div class="read">READ MORE →</div></article>
    <article class="post"><div class="pic post3" role="img" aria-label="Hand holding a small cannabis plant"></div><h3>Lorem ipsum dolor sit amet or sit amet adipiscing elit, sed do eiusmod tempor</h3><p>Lorem ipsum dolor sit amet, consectetur adipiscing elit, sed do eiusmod tempor incididunt ut labore et dolore magna aliqua.</p><div class="read">READ MORE →</div></article>
  </div>
  <a class="btn">View all posts</a>
</section>

<footer class="footer">
  <div class="footer-cols">
    <div>
      <h4>About the shop</h4>
      <p>Lorem ipsum dolor sit amet, consectetur adipiscing elit, sed do eiusmod tempor incididunt.</p>
      <p>Lorem ipsum dolor sit amet, consectetur adipiscing elit, sed do eiusmod tempor incididunt ut labore et dolore magna.</p>
      <div class="contact"><svg width="14" height="12" viewBox="0 0 14 12"><rect x="0.5" y="0.5" width="13" height="11" fill="none" stroke="#cfcad8"/><path d="M1 1l6 5 6-5" fill="none" stroke="#cfcad8"/></svg>hello@velvetorbit.com</div>
      <div class="contact"><svg width="14" height="14" viewBox="0 0 24 24"><path d="M6.6 10.8a15 15 0 006.6 6.6l2.2-2.2c.3-.3.7-.4 1-.2 1.1.4 2.3.6 3.6.6.6 0 1 .4 1 1V20c0 .6-.4 1-1 1C10.6 21 3 13.4 3 4c0-.6.4-1 1-1h3.5c.6 0 1 .4 1 1 0 1.3.2 2.5.6 3.6.1.3 0 .7-.2 1z" fill="#cfcad8"/></svg>Call &amp; Text: 000 555 0100</div>
      <div class="social"><span></span><span></span><span></span><span></span></div>
    </div>
    <div>
      <h4>Menu</h4>
      <ul><li>About Us</li><li>Terms &amp; Conditions</li><li>Shipping &amp; Returns</li><li>Privacy Policy</li><li>Disclaimer</li><li>Contact Us</li><li>CBD Flower Wholesale</li><li>CBD Hemp FAQ</li><li>CBD / Hemp Lab Tests</li></ul>
    </div>
    <div>
      <h4>Get the drop</h4>
      <p>Join our newsletter and get updated on new products, strains, and trends.</p>
      <div class="field">Enter your Email Address</div>
      <a class="btn">Subscribe</a>
    </div>
  </div>
  <div class="copy">2020 VELVET ORBIT. All Rights Reserved.</div>
</footer>

</body>
</html>
```